Dental specialist needs a sharp looking letterhead

I am looking for a letterhead to be used to send letters and communication between myself (a dental specialist) and other dentists.
My office is a state of the art dental specialty office.
I need to letterhead to also state:
Bertram L. Oswick DDS
2748 Tollard Avenue, Suite K
West Tollard, NY 14391
(716)392-5061
fax: (716)392-5087
oswickroot.com (**this email address may change)

i included my logo designs.
thank you

Target Market(s)

dentists

Industry/Entity Type

Communication

Requirements
Must have
• the included logo, whether the vertical or horizontal versions

```html
<!DOCTYPE html>
<html lang="en">
<head>
<meta charset="utf-8">
<title>Aldercrest Endodontics P.C. — Letterhead</title>
<link href="https://fonts.googleapis.com/css2?family=Roboto+Slab:wght@400;600&display=swap" rel="stylesheet">
<style>
  :root {
    --brand-blue: #42a1db;
    --brand-green: #8cc63f;
    --ink: #1a1a1a;
    --ink-soft: #3a3a3a;
    --rule: #555555;
    --paper: #ffffff;
  }
  * { margin: 0; padding: 0; box-sizing: border-box; }
  html, body { width: 931px; height: 1200px; overflow: hidden; background: var(--paper); }
  .letterhead {
    position: relative;
    width: 931px;
    height: 1200px;
    background: var(--paper);
    font-family: "Roboto Slab", Georgia, serif;
    color: var(--ink);
  }
  .brand {
    position: absolute;
    left: 43px;
    top: 44px;
    height: 94px;
    display: flex;
    align-items: center;
  }
  .brand-dot {
    width: 76px;
    height: 76px;
    border-radius: 50%;
    background: var(--brand-blue);
    margin-right: 10px;
  }
  .brand-rule {
    width: 1px;
    height: 94px;
    background: var(--rule);
    margin-right: 8px;
  }
  .brand-name {
    font-weight: 600;
    color: var(--ink);
    line-height: 1;
  }
  .brand-name .primary { display: block; font-size: 28px; letter-spacing: 0.2px; }
  .brand-name .secondary { display: block; font-size: 13.5px; letter-spacing: 2px; margin-top: 6px; padding-left: 24px; }

  .contact {
    position: absolute;
    left: 651px;
    top: 41px;
    height: 96px;
    border-left: 1px solid var(--rule);
    padding-left: 12px;
  }
  .contact-name { font-size: 19.5px; font-weight: 400; color: var(--ink); line-height: 1; margin-top: 6px; }
  .contact-name .degree { color: var(--brand-green); }
  .contact-list { list-style: none; margin-top: 10px; }
  .contact-list li {
    display: flex;
    align-items: center;
    font-size: 15px;
    color: var(--ink-soft);
    line-height: 21px;
  }
  .contact-list svg { width: 14px; height: 14px; margin-right: 5px; flex: none; }

  .address {
    position: absolute;
    left: 0;
    right: 0;
    top: 1144px;
    display: flex;
    justify-content: center;
    align-items: center;
    font-size: 18.5px;
    color: var(--ink-soft);
    transform: translateX(-1px);
  }
  .address svg { width: 14px; height: 19px; margin-right: 12px; }

  .footer-band { position: absolute; left: 0; bottom: 0; width: 931px; height: 22px; }
</style>
</head>
<body>
<main class="letterhead">
  <header class="brand">
    <span class="brand-dot"></span>
    <span class="brand-rule"></span>
    <h1 class="brand-name">
      <span class="primary">ALDERCREST</span>
      <span class="secondary">Endodontics P.C.</span>
    </h1>
  </header>

  <aside class="contact">
    <p class="contact-name">Bertram L. Oswick<span class="degree">, DDS</span></p>
    <ul class="contact-list">
      <li>
        <svg viewBox="0 0 14 14" aria-hidden="true"><circle cx="7" cy="7" r="6" fill="none" stroke="var(--brand-blue)" stroke-width="1.3"/><path d="M5 4 Q4 7 6.5 10 L8 9 L7 7.5 L6.3 8 Q5.6 6.8 6 5.6 L6.8 5.4 L6.5 3.8 Z" fill="var(--brand-blue)"/></svg>
        716-392-5061
      </li>
      <li>
        <svg viewBox="0 0 14 14" aria-hidden="true"><rect x="4" y="2" width="6" height="4" fill="var(--brand-green)"/><rect x="1" y="5.5" width="12" height="5.5" rx="1.5" fill="var(--brand-green)"/><rect x="4" y="9" width="6" height="3" fill="#ffffff"/></svg>
        716-392-5087
      </li>
      <li>
        <svg viewBox="0 0 14 14" aria-hidden="true"><rect x="1" y="3" width="12" height="8.5" fill="var(--brand-blue)"/><path d="M1 3 L7 8 L13 3" fill="none" stroke="#ffffff" stroke-width="1.2"/></svg>
        office@oswickroot.com
      </li>
    </ul>
  </aside>

  <p class="address">
    <svg viewBox="0 0 14 19" aria-hidden="true"><path d="M7 0 C3 0 0 3 0 7 C0 12 7 19 7 19 C7 19 14 12 14 7 C14 3 11 0 7 0 Z" fill="var(--ink-soft)"/><circle cx="7" cy="7" r="2.6" fill="#ffffff"/></svg>
    2748 Tollard Avenue, Suite K, West Tollard, NY 14391
  </p>

  <svg class="footer-band" viewBox="0 0 931 22" preserveAspectRatio="none" aria-hidden="true">
    <polygon points="0,0 444,0 397,22 0,22" fill="var(--brand-blue)"/>
    <polygon points="456,0 931,0 931,22 410,22" fill="var(--brand-green)"/>
  </svg>
</main>
</body>
</html>
```